Small Business Directory Site Requires a Professional Responsive Web Design

Small Business Directory and Coupon Site - we require a complete website design for a brand new responsive & mobile friendly website. We already have a coder who will professional code our website in Magento.

All PSD pages need to be professionally designed then uploaded into a sharedrive (i.e. like filecrate). Additionally, as I cannot pre-empt everything, please note that we may require a little more assistance once the files have been transferred (for example, in www.brightlane-listings.example if you hover your mouse on the search box you will see a pop up box. We want one of these too and I think that means there may be extra design work here)

We have some draft page sketches have been created (there are some minor changes we want to the sketches provided though); however, we require an excellent designer to add the creative touches to it to make it look professionally created. All artwork/font must be legal.

-------------------------
We like the look of the www.brightlane-listings.example and www. marlowfolio.example

For the headers, please consider a font similar to RNS camellia. We likes this style, but it is too thin for the headers...so we need a variation like this one. For the copy/general text font, something basic that marries well with the headers.

---------------------

Please be sure to also read the brief we wrote for the coder as this will help with better understanding our design requirements.

In total I believe we have about 50 pages. This includes all the little pages and most of the pop up boxes (but not the little help key boxes). For example, pages include...

1. Login (this is where customers log in and can edit, manage their profiles. This means that there are backend membership pages)
2. Mini Services (same look and feel as the business coupons)
3. Resource Centre
4. Join (this is where customers learn about the packages available to submit a directory listing, if they ‘buy’ a package (i.e. free, $25 or $150 package) then they can create their own directory listing)
5. Search the directory (customer can view all the categories and also search the directory)
6. Create a directory listing (this is where customers learn about the packages available to submit a directory listing, if they ‘buy’ a package (i.e. free, $25 or $150 package) then they can create their own directory listing)
7. Quote finder (also know as Get a Quote)
8. Coupons (customer go to the business coupon page and can view all current coupons/submit a coupon)
9. Submit a coupon (form)
10.Advertise with us (form)
11. Join the forum
12.Submit an article or video (form)
13. Affiliates (listing of affiliates we currently have)
14. Become an affiliate (form)
15. Case studies (customer can view the case studies we have in the resource centre)
16. Help Guides (customer can view the help guides we have in the resource centre)
17. About Us
18 .Contact Us (form)
19. Terms & Condition
20. Privacy Policy
21. Supporting City Councils
22. Site Map
23. Forgot password / login details
24. Homepage
25. If we hover over a few areas (i.e. search box, location field) it pops up with more information.
etc etc etc. . . there are more pages.

Please see our filecrate link for the draft mock up pages that I have created so far.

https://www.cloudtrunk.example/sh/qk72pmw4rtz8nd/KLMvbTq2fWndxPzs8Yh4ecRQu

We are in a rush! We'd like to get the majority of the artwork completed by the end of the month. Minor fixes/tweaks can occur thereafter.

Target Market(s)

Small Businesses (employees 0 - 50) located throughout Australia

Industry/Entity Type

Business

Font styles to use
Sans Serif

Requirements
Must have
• Professional. Artwork must be legal (cannot be cut and paste or taken off other websites, must be legally purchased and used).Must look contemporary, fresh, modern.

Absolutely must be a responsive site!
Nice to have
• original work, original photos, original art.

like modern, fresh photos that demonstrate innovation, growth, small business, Australian scenery, stability, goals/passion.
Should not have
• cut and paste graphics, illegal graphics, not purchased graphics.

```html
<!DOCTYPE html>
<html lang="en">
<head>
<meta charset="utf-8">
<title>Bizbridge Hub – Small Business Directory</title>
<link href="https://fonts.googleapis.com/css2?family=PT+Sans:wght@400;700&display=swap" rel="stylesheet">
<style>
:root{
  --orange:#f36b0c;
  --black:#000;
  --footer:#121212;
  --footer-bottom:#0a0a0a;
  --cream:#f4f1ec;
  --text:#333;
  --muted:#999;
  --white:#fff;
  --navy:#0d2f57;
}
*{box-sizing:border-box;margin:0;padding:0}
html,body{width:976px;height:1200px;overflow:hidden}
body{font-family:"PT Sans",Arial,sans-serif;background:var(--white);position:relative;color:var(--text)}

/* header */
.site-header{position:absolute;left:0;top:0;width:976px;height:84px;background:var(--black)}
.brand{position:absolute;left:148px;top:20px;display:flex;align-items:center;gap:8px}
.brand-mark{width:22px;height:22px;background:var(--orange);border-radius:3px}
.brand-name{color:var(--white);font-size:19px;font-weight:400;letter-spacing:.3px}
.field{position:absolute;top:28px;height:30px;border:1px solid var(--white);color:var(--white);font-size:10px;padding:9px 14px}
.field.search{left:403px;width:144px}
.field.near{left:563px;width:102px}
.search-btn{position:absolute;left:680px;top:28px;width:32px;height:30px;background:var(--orange);border-radius:3px}
.account{position:absolute;left:747px;top:34px;color:var(--white);font-size:10px;word-spacing:3px}

/* hero */
.hero{position:absolute;left:0;top:84px;width:976px;height:384px;
  background:radial-gradient(ellipse at 38% 45%,#d69a3a 0%,#b9742a 30%,#7d4a1f 62%,#3e2514 100%)}
.hero-title{position:absolute;left:124px;top:127px;color:var(--white);font-size:31px;font-weight:700;text-shadow:1px 2px 3px rgba(0,0,0,.5);white-space:nowrap}
.hero-sub{position:absolute;left:124px;top:177px;color:var(--white);font-size:20px;font-weight:700;text-shadow:1px 2px 3px rgba(0,0,0,.5);white-space:nowrap}
.btn{position:absolute;background:var(--orange);color:var(--white);border-radius:3px;text-align:center;box-shadow:0 2px 4px rgba(0,0,0,.35);white-space:nowrap}
.btn.join{left:126px;top:222px;width:91px;height:32px;line-height:32px;font-size:11px}
.directory-panel{position:absolute;left:604px;top:62px;width:246px;height:246px;background:rgba(40,25,15,.55)}
.directory-frame{position:absolute;left:12px;top:2px;width:222px;height:230px;border:1px solid rgba(255,255,255,.6)}
.directory-title{position:absolute;left:0;top:18px;width:100%;text-align:center;color:var(--white);font-size:30px;font-weight:700}
.directory-text{position:absolute;left:12px;top:76px;width:198px;color:var(--white);font-size:9.4px;line-height:18px;text-align:justify;text-align-last:center}
.btn.listing{left:20px;top:168px;width:182px;height:38px;line-height:38px;font-size:13px}
.dots{position:absolute;left:462px;top:347px;display:flex;gap:5px}
.dots span{width:10px;height:10px;border-radius:50%;background:var(--white)}
.dots span.active{box-shadow:0 0 0 2px rgba(255,255,255,.6);border:2px solid #8a5a2c}

/* community */
.community{position:absolute;left:0;top:468px;width:976px;height:392px;background:var(--cream)}
.section-title{position:absolute;left:0;top:32px;width:100%;text-align:center;font-size:17px;font-weight:700;color:var(--black)}
.section-rule{position:absolute;left:357px;top:59px;width:268px;height:2px;background:var(--orange)}
.feature{position:absolute;top:88px;width:230px;text-align:center}
.feature h3{color:var(--orange);font-size:13px;font-weight:400;margin-bottom:12px;white-space:nowrap}
.feature p{font-size:8.6px;line-height:16.8px;color:var(--text);white-space:nowrap}
.feature.one{left:138px}.feature.two{left:374px}.feature.three{left:611px}
.tile{position:absolute;top:206px;width:208px;height:152px;border:1px solid #ccc}
.tile.one{left:146px;background:linear-gradient(135deg,#e6edf3,#9fb3c6 55%,#2b4b78)}
.tile.two{left:383px;background:linear-gradient(135deg,#d9dde2,#eef1f4 50%,#8fb1d3)}
.tile.three{left:621px;background:var(--white);display:flex;align-items:center;justify-content:center;gap:8px}
.play{position:absolute;left:86px;top:58px;width:34px;height:34px;border-radius:50%;background:#111;border:2px solid var(--white)}
.play::after{content:"";position:absolute;left:13px;top:10px;border-left:9px solid var(--white);border-top:6px solid transparent;border-bottom:6px solid transparent}
.partner-dot{width:28px;height:28px;border-radius:50%;background:var(--navy)}
.partner-name{color:var(--navy);font-size:26px;font-weight:700;white-space:nowrap}

/* partners band */
.partners{position:absolute;left:0;top:860px;width:976px;height:90px;background:var(--orange);display:flex;justify-content:center;align-items:center;gap:110px}
.partners span{color:var(--white);font-size:30px;font-weight:700}

/* footer */
.site-footer{position:absolute;left:0;top:950px;width:976px;height:197px;background:var(--footer)}
.foot-col{position:absolute;top:30px}
.foot-col h4{color:var(--white);font-size:13px;font-weight:400;margin-bottom:16px;white-space:nowrap}
.foot-col ul{list-style:none}
.foot-col li{color:var(--muted);font-size:9px;line-height:17.5px;padding-left:14px;position:relative;white-space:nowrap}
.foot-col li::before{content:"";position:absolute;left:0;top:5px;border-left:4px solid var(--muted);border-top:3px solid transparent;border-bottom:3px solid transparent}
.c1{left:148px}.c2{left:284px}.c3{left:419px}.c4{left:585px}.c5{left:694px}
.social{display:flex;gap:10px;margin-top:-2px}
.social span{width:25px;height:25px;border-radius:50%;border:1px solid #777}
.copyright{position:absolute;left:0;top:1147px;width:976px;height:53px;background:var(--footer-bottom);color:var(--muted);font-size:9px;text-align:center;line-height:53px}
</style>
</head>
<body>

<header class="site-header">
  <div class="brand"><span class="brand-mark"></span><span class="brand-name">Bizbridge Hub</span></div>
  <div class="field search">Search</div>
  <div class="field near">Near</div>
  <div class="search-btn">
    <svg width="32" height="30" viewBox="0 0 32 30"><circle cx="14" cy="13" r="5" fill="none" stroke="#fff" stroke-width="1.6"/><line x1="18" y1="17" x2="22" y2="21" stroke="#fff" stroke-width="2"/></svg>
  </div>
  <div class="account">LOGIN &nbsp;| &nbsp;JOIN</div>
</header>

<section class="hero" role="img" aria-label="Photo of warm orange sandstone rock layers">
  <h1 class="hero-title">LET US HELP YOU GROW</h1>
  <h2 class="hero-sub">AUSTRALIA’S SMALL BUSINESS BRIDGE HUB</h2>
  <div class="btn join">JOIN TODAY</div>
  <div class="directory-panel">
    <div class="directory-frame">
      <div class="directory-title">DIRECTORY</div>
      <p class="directory-text">Our small business directory is maintained to give members choice. We’re open to all businesses, regardless of your location, so long as they service Australian small businesses.</p>
      <div class="btn listing">CREATE YOUR FREE LISTING</div>
    </div>
  </div>
  <div class="dots"><span class="active"></span><span></span><span></span><span></span></div>
</section>

<section class="community">
  <h2 class="section-title">GET REAL SUPPORT FROM OUR COMMUNITY</h2>
  <div class="section-rule"></div>
  <div class="feature one">
    <h3>How Did You Sort Your Business?</h3>
    <p>Learn from Dana Pellwood, a real small business owner.<br>How she started her business and what are<br>the most valuable resources for her<br>right now.</p>
  </div>
  <div class="feature two">
    <h3>Why Go with Bizbridge Hub?</h3>
    <p>What small business owner can’t relate to the ongo-<br>ing task of attracting new customers? Struggling<br>with cash flow? Or how about not having<br>enough time in the day?</p>
  </div>
  <div class="feature three">
    <h3>Become an Affiliate</h3>
    <p>If you have a network of small businesses, let us help<br>to create additional value for your members and<br>make money for your network. Talk to us<br>today about how we can help.</p>
  </div>
  <div class="tile one" role="img" aria-label="Photo of two business people working at a laptop"></div>
  <div class="tile two" role="img" aria-label="Video still of a small business owner using a calculator at a desk"><span class="play"></span></div>
  <div class="tile three"><span class="partner-dot"></span><span class="partner-name">Harbor Cover</span></div>
</section>

<section class="partners">
  <span>Corvell</span>
  <span>Tandemdesk</span>
  <span>Orvik</span>
</section>

<footer class="site-footer">
  <div class="foot-col c1"><h4>SITE DIRECTORY</h4><ul>
    <li>Search the Directory</li><li>Create a Directory Listing</li><li>Quote Finder</li><li>Coupons</li><li>Submit a Coupon</li><li>Advertise with Us</li></ul></div>
  <div class="foot-col c2"><h4>RESOURCES</h4><ul>
    <li>Join the Forum</li><li>Submit an Article</li><li>Affiliates</li><li>Become an Affiliate</li><li>Case Studies</li><li>Help Guides</li></ul></div>
  <div class="foot-col c3"><h4>POPULAR CATEGORIES</h4><ul>
    <li>Join the Forum</li><li>Submit an Article</li><li>Affiliates</li><li>Become an Affiliate</li><li>Case Studies</li><li>Help Guides</li></ul></div>
  <div class="foot-col c4"><h4>ABOUT</h4><ul>
    <li>About Us</li><li>Contact Us</li><li>Terms &amp; Condition</li><li>Privacy Polacy</li><li>Supporting City</li><li>Site Map</li></ul></div>
  <div class="foot-col c5"><h4>FOLLOW US</h4>
    <div class="social"><span aria-label="Social link"></span><span aria-label="Social link"></span><span aria-label="Social link"></span><span aria-label="Social link"></span></div></div>
</footer>
<div class="copyright">© copy right 2014 bizbridgehub . All rights reserved.</div>

</body>
</html>
```